Automotive component supplier needs a business card design

We need a business card design for our company called Velran Global Components Ltd based in the UK. We are a supplier of interior and exterior components to premium car manufacturers such as Corvel Ashby, Hadley Fenn, Marquist and Tavarelli. We would like to see a modern business card design that uses the colour blue.

Target Market(s)

Premium automotive car manufacturers.

Industry/Entity Type

Automotive

Contact Information for Business Card

Company Name : Velran Global Components Limited
Address: 17 Marlow Yard, Upper Heath, Warwick, CV31 8QL, United Kingdom
Web Address : www.velrancomponents-example.co.uk

Font styles to use
Other font styles liked:
• Helvetica

Colors
3176b5
0255a3
85acd3
cfdeed
cee9f5
85cae6
34a6d7
0692cd
9bcb3c

Requirements
Must have
• Clear company logo and a mixture of blue colours.
Nice to have
• A high quality modern image.
Should not have
• Multiple colours.

```html
<!DOCTYPE html>
<html lang="en">
<head>
<meta charset="utf-8">
<title>Velran Global Components – Business Card</title>
<link rel="stylesheet" href="https://fonts.googleapis.com/css2?family=Arimo:wght@400;700&display=swap">
<style>
  :root {
    --stage: #2e2e2e;
    --paper: #ffffff;
    --paper-shade: #e9e9e9;
    --brand-blue: #0a84c6;
    --deep-blue: #0255a3;
    --card-blue: #0e93d2;
    --card-blue-dark: #0b86c2;
    --accent-green: #8dc63f;
    --ink: #5b5b5b;
    --rule: #3d6b3a;
    --white: #ffffff;
  }
  * { box-sizing: border-box; margin: 0; padding: 0; }
  html, body { width: 1200px; height: 965px; overflow: hidden; }
  body {
    background: var(--stage);
    font-family: "Arimo", Helvetica, Arial, sans-serif;
    position: relative;
  }
  .card {
    position: absolute;
    left: 246px;
    width: 710px;
    height: 403px;
  }
  /* Front */
  .card--front {
    top: 60px;
    background: radial-gradient(ellipse at 45% 35%, var(--paper) 40%, var(--paper-shade) 100%);
  }
  .wordmark {
    position: absolute;
    left: 44px;
    top: 158px;
    width: 336px;
    color: var(--brand-blue);
    font-weight: 700;
  }
  .wordmark__name {
    display: flex;
    align-items: center;
    gap: 12px;
    font-size: 70px;
    line-height: 1;
    letter-spacing: 2px;
  }
  .wordmark__dot {
    width: 16px; height: 16px;
    background: var(--accent-green);
    flex: none;
  }
  .wordmark__tag {
    margin-top: 10px;
    font-size: 15.5px;
    letter-spacing: 2.4px;
    white-space: nowrap;
  }
  .divider {
    position: absolute;
    left: 414px;
    top: 60px;
    width: 2px;
    height: 280px;
    background: linear-gradient(to bottom, transparent, var(--rule) 20%, var(--rule) 80%, transparent);
  }
  .contact {
    position: absolute;
    left: 444px;
    top: 82px;
    color: var(--ink);
  }
  .contact__name {
    color: var(--brand-blue);
    font-size: 23px;
    font-weight: 700;
    letter-spacing: 0.3px;
  }
  .contact__role {
    color: var(--accent-green);
    font-size: 16px;
    margin-top: 1px;
  }
  .contact__list {
    list-style: none;
    margin-top: 26px;
    font-size: 13.5px;
    line-height: 20px;
  }
  .contact__list li { display: flex; align-items: center; gap: 9px; }
  .contact__list svg { width: 16px; height: 16px; flex: none; }
  .contact__address {
    margin-top: 26px;
    font-size: 15.5px;
    line-height: 20px;
    font-style: normal;
  }
  /* Back */
  .card--back {
    top: 504px;
    background: var(--card-blue);
    color: var(--white);
    overflow: hidden;
  }
  .card__texture {
    position: absolute; inset: 0;
    background: linear-gradient(180deg, var(--card-blue-dark), var(--card-blue) 50%, var(--card-blue-dark));
  }
  .back-mark {
    position: absolute;
    left: 0; right: 0;
    top: 128px;
    text-align: center;
    font-weight: 700;
  }
  .back-mark__name {
    font-size: 112px;
    line-height: 1;
    letter-spacing: 4px;
  }
  .back-mark__tag {
    margin-top: 18px;
    font-size: 27px;
    letter-spacing: 3px;
  }
  .back-url {
    position: absolute;
    left: 0; right: 0;
    top: 369px;
    display: flex;
    align-items: center;
    justify-content: center;
    gap: 14px;
    font-size: 14.5px;
  }
  .back-url__line { width: 190px; height: 2px; background: rgba(255,255,255,0.85); }
</style>
</head>
<body>
  <section class="card card--front" aria-label="Card front">
    <div class="wordmark">
      <div class="wordmark__name">VELRAN<span class="wordmark__dot"></span></div>
      <div class="wordmark__tag">GLOBAL COMPONENTS</div>
    </div>
    <div class="divider"></div>
    <div class="contact">
      <div class="contact__name">DORIAN KELL</div>
      <div class="contact__role">Founder &amp; CEO</div>
      <ul class="contact__list">
        <li>
          <svg viewBox="0 0 16 16" fill="var(--brand-blue)"><rect x="1" y="2" width="4" height="12" rx="1"/><rect x="6" y="2" width="9" height="12" rx="1"/><rect x="8" y="4" width="5" height="2" fill="#fff"/><rect x="8" y="8" width="5" height="4" fill="#fff"/></svg>
          + 041 555 01 27
        </li>
        <li>
          <svg viewBox="0 0 16 16" fill="var(--brand-blue)"><rect x="4" y="1" width="8" height="14" rx="1.5"/><rect x="5.5" y="3" width="5" height="8" fill="#fff"/><circle cx="8" cy="13" r="0.9" fill="#fff"/></svg>
          + 0164 555 03 48
        </li>
        <li>
          <svg viewBox="0 0 16 16"><rect x="1" y="3.5" width="14" height="9" fill="var(--brand-blue)"/><path d="M1 3.5 L8 9 L15 3.5 M1 12.5 L6 8 M15 12.5 L10 8" stroke="#fff" stroke-width="1.2" fill="none"/></svg>
          info@velrancomponents-example.co.uk
        </li>
        <li>
          <svg viewBox="0 0 16 16" fill="none" stroke="var(--brand-blue)" stroke-width="1.3"><circle cx="8" cy="8" r="6.5"/><ellipse cx="8" cy="8" rx="3" ry="6.5"/><path d="M1.5 8h13M2.5 5h11M2.5 11h11"/></svg>
          www.velrancomponents-example.co.uk
        </li>
      </ul>
      <address class="contact__address">
        17 Marlow Yard, Upper Heath,<br>
        Warwick, CV31 8QL,<br>
        United Kingdom
      </address>
    </div>
  </section>

  <section class="card card--back" aria-label="Card back">
    <div class="card__texture" role="img" aria-label="Repeating tone-on-tone brand name pattern in blue"></div>
    <div class="back-mark">
      <div class="back-mark__name">VELRAN</div>
      <div class="back-mark__tag">GLOBAL COMPONENTS</div>
    </div>
    <div class="back-url">
      <span class="back-url__line"></span>
      <span>www.velrancomponents-example.co.uk</span>
      <span class="back-url__line"></span>
    </div>
  </section>
</body>
</html>
```